Mira Bloom Fitness Coaching Project

I am a personal trainer based in London. My services include one-on-one PT sessions, bootcamps.
I would like the design to be minimalistic. With light colours: white, pink, purple.
I specialise in weight loss, flexibility, mobility.

Tessa Brogan
Personal Trainer
Email: tessa.brogan@quellmail.com
tel: 07700218493
Instagram: Mira Bloom

Target Market(s)

adults, mostly females (age 18-50).

Industry/Entity Type

Fitness

Contact Information for Business Card

Tessa Brogan
Personal Trainer
tel: 07700218493
Instagram: Mira Bloom

Font styles to use
Serif

Colors
eea4c8
fbd4d5
fdf9cf
cfeae6
cee9f5

Requirements
Nice to have
• minimalistic style
• easy to read and remember

```html
<!DOCTYPE html>
<html lang="en">
<head>
<meta charset="utf-8">
<title>Tessa Brogan – Personal Trainer Business Card</title>
<link rel="stylesheet" href="https://fonts.googleapis.com/css2?family=Bodoni+Moda:wght@500&family=Raleway:wght@300&family=EB+Garamond:wght@400&display=swap">
<style>
  :root {
    --page-bg: #e9e7e8;
    --front-dark: #0f1710;
    --front-green: #1f3320;
    --photo-warm: #8a5a34;
    --photo-light: #d9b48a;
    --photo-deep: #2a2a1c;
    --name-white: #f4f2f0;
    --back-white: #f7f7f7;
    --back-grey: #dcdcdc;
    --ink: #1c1c1c;
    --accent-pink: #eea4c8;
  }
  * { margin: 0; padding: 0; box-sizing: border-box; }
  html, body { width: 1200px; height: 997px; overflow: hidden; }
  body {
    background: var(--page-bg);
    display: flex;
    flex-direction: column;
    align-items: center;
    justify-content: center;
    gap: 48px;
  }
  .card {
    position: relative;
    width: 760px;
    height: 434px;
    border-radius: 26px;
    overflow: hidden;
    box-shadow: 0 14px 34px rgba(0,0,0,0.22);
  }
  /* Front */
  .card-front {
    background: radial-gradient(circle at 30% 60%, var(--front-green) 0%, var(--front-dark) 65%);
  }
  .portrait {
    position: absolute;
    top: 0;
    right: 0;
    width: 430px;
    height: 100%;
    background:
      radial-gradient(ellipse at 45% 40%, var(--photo-light) 0%, var(--photo-warm) 38%, rgba(42,42,28,0.6) 70%, rgba(15,23,16,0) 100%),
      linear-gradient(90deg, var(--front-dark) 0%, var(--photo-deep) 40%, var(--photo-deep) 100%);
  }
  .identity {
    position: absolute;
    left: 70px;
    top: 238px;
    color: var(--name-white);
  }
  .identity-name {
    font-family: "Bodoni Moda", serif;
    font-weight: 500;
    font-size: 34px;
    letter-spacing: 0.5px;
    line-height: 1;
  }
  .identity-role {
    font-family: "Raleway", sans-serif;
    font-weight: 300;
    font-size: 15px;
    letter-spacing: 5px;
    margin-top: 8px;
    padding-left: 52px;
  }
  /* Back */
  .card-back {
    background: linear-gradient(135deg, var(--back-white) 0%, var(--back-grey) 45%, var(--back-white) 70%, var(--back-grey) 100%);
  }
  .facet-texture {
    position: absolute;
    inset: 0;
    background:
      linear-gradient(160deg, rgba(255,255,255,0.6) 0%, rgba(255,255,255,0) 50%),
      linear-gradient(20deg, rgba(200,200,200,0.35) 0%, rgba(255,255,255,0) 60%);
  }
  .contact-list {
    position: absolute;
    left: 68px;
    top: 290px;
    font-family: "EB Garamond", serif;
    font-size: 24px;
    color: var(--ink);
    display: grid;
    grid-template-columns: auto auto;
    column-gap: 30px;
    row-gap: 14px;
  }
  .contact-item { display: flex; align-items: center; gap: 8px; }
  .contact-item.wide { grid-column: 1 / 3; }
  .contact-icon { width: 16px; height: 16px; flex: none; }
  .square-mark { width: 14px; height: 14px; background: var(--accent-pink); border-radius: 3px; flex: none; }
</style>
</head>
<body>
  <section class="card card-front">
    <div class="portrait" role="img" aria-label="Portrait photo of the trainer with long curly hair, backlit, against dark green foliage"></div>
    <div class="identity">
      <div class="identity-name">TESSA BROGAN</div>
      <div class="identity-role">Personal Trainer</div>
    </div>
  </section>

  <section class="card card-back">
    <div class="facet-texture" role="img" aria-label="Soft light grey faceted background texture"></div>
    <div class="contact-list">
      <div class="contact-item">
        <svg class="contact-icon" viewBox="0 0 16 16" aria-hidden="true">
          <path d="M4 1.5 L6 5 L4.5 6.5 C5.5 8.5 7.5 10.5 9.5 11.5 L11 10 L14.5 12 L13 14.5 C7 14 2 9 1.5 3 Z" fill="var(--accent-pink)"/>
        </svg>
        <span>07700218493</span>
      </div>
      <div class="contact-item">
        <svg class="contact-icon" viewBox="0 0 16 16" aria-hidden="true">
          <rect x="1" y="3" width="14" height="10" rx="1" fill="var(--accent-pink)"/>
          <path d="M1.5 3.5 L8 9 L14.5 3.5" fill="none" stroke="#fff" stroke-width="1.2"/>
        </svg>
        <span>tessa.brogan@quellmail.com</span>
      </div>
      <div class="contact-item wide">
        <span class="square-mark"></span>
        <span>picfeed.com/Mira_Bloom</span>
      </div>
    </div>
  </section>
</body>
</html>
```